Tidewater Motion Bodywork needs a Website

I'm a Massage Practitioner wanting a website for promotion and bookings with a Blog area and inplementation to my facebook page https://www.pagewall-social.com/TidewaterMotionBodywork , my setmore Booking page http://my.slotkeeper.net/bookingpage/a73e2d41-5b6c-4e82-9f07-c18d25e6b3a0 and my PayPal account to make payments.
The Venues changes from time to time. In October 2015 it will be the Coralspan Endurance Worldchampionship in Kona Hawaii

Target Market(s)

Sports People participating in targeted Events

Industry/Entity Type

Massage

Number of Pages Required

5+ page

Font styles to use
Other font styles liked:
• Verdana

Colors
3176b5
5db8de
ec1f27
ffffff

Requirements
Must have
• An About page including which events (in this case Coralspan Endurance World Championship in Kona, Hawaii in October 2015)
• A page with the Techniques I use
• Inplementation of my Setmore Booking Page http://my.slotkeeper.net/bookingpage/a73e2d41-5b6c-4e82-9f07-c18d25e6b3a0
• Implementation of my Facebook Page https://www.pagewall-social.com/TidewaterMotionBodywork
Nice to have
• Would be great to have a Blog with Pictures Upload ability
• Tried to upload Pictures but it always says that it is a non supported file type, so contact me to send you those informations. More informations about me to be found on http://wellroot.com.au/about-us/meet-the-team/jon-harlow-pike---massage-therapist.html

```html
<!DOCTYPE html>
<html lang="en">
<head>
<meta charset="utf-8">
<title>Tidewater Motion Bodywork</title>
<link href="https://fonts.googleapis.com/css2?family=Open+Sans:ital,wght@0,300;0,400;0,600;1,400&display=swap" rel="stylesheet">
<style>
  :root {
    --brand-blue: #3176b5;
    --sky-blue: #5db8de;
    --band-blue: #7fcdf0;
    --accent-red: #ec1f27;
    --white: #ffffff;
    --ink: #555a5e;
    --ink-soft: #8a8f93;
    --rule: #dcdfe2;
    --footer-bg: #eeeff0;
  }
  * { box-sizing: border-box; margin: 0; padding: 0; }
  html, body { width: 850px; height: 1200px; overflow: hidden; background: var(--white); }
  body { position: relative; font-family: "Open Sans", Verdana, sans-serif; color: var(--ink); }
  .abs { position: absolute; }

  /* header */
  .site-header { left: 0; top: 0; width: 850px; height: 76px; background: var(--white); box-shadow: 0 2px 3px rgba(0,0,0,.12); z-index: 2; }
  .brand { left: 70px; top: 26px; display: flex; align-items: center; gap: 8px; }
  .brand-dot { width: 22px; height: 22px; border-radius: 50%; background: var(--sky-blue); }
  .brand-name { font-size: 13px; font-weight: 400; color: var(--accent-red); }
  .main-nav { right: 70px; top: 28px; display: flex; gap: 27px; font-size: 10.5px; }
  .main-nav a { color: var(--ink); text-decoration: none; }
  .main-nav a.is-current { color: var(--accent-red); }

  /* hero */
  .hero-band { left: 0; top: 76px; width: 850px; height: 358px; background: var(--band-blue); }
  .slider-frame { left: 70px; top: 141px; width: 710px; height: 364px; background: var(--white); box-shadow: 0 10px 14px rgba(0,0,0,.18); }
  .slider-photo { left: 8px; top: 8px; width: 693px; height: 346px; background: linear-gradient(120deg, #6b6f78 0%, #c9b9a6 40%, #b23a45 62%, #d9d6c8 85%, #a7b58a 100%); }
  .slider-controls { right: 9px; bottom: 10px; width: 39px; height: 27px; background: rgba(255,255,255,.75); }

  /* intro */
  .section-title { font-size: 20px; font-weight: 400; color: var(--ink); }
  .intro-photo { left: 70px; top: 583px; width: 182px; height: 131px; background: linear-gradient(160deg, #8c939a, #d7d2cc 55%, #5e6b4f); }
  .intro-text { left: 272px; top: 582px; width: 272px; font-size: 8.4px; line-height: 15.9px; color: var(--ink-soft); }
  .btn { display: block; width: 65px; height: 26px; line-height: 26px; text-align: center; background: var(--brand-blue); color: var(--white); font-size: 8px; font-weight: 600; border-radius: 2px; text-decoration: none; }
  .quote { left: 592px; top: 579px; width: 182px; font-size: 8.6px; line-height: 14.5px; font-style: italic; color: var(--brand-blue); }
  .quote-mark { color: #c3c7ca; font-size: 14px; font-style: normal; font-weight: 600; }
  .quote-author { left: 589px; top: 665px; font-size: 7.8px; color: var(--ink); font-weight: 600; }

  .divider { left: 70px; top: 753px; width: 710px; height: 1px; background: var(--rule); }

  /* services */
  .service { width: 218px; }
  .service-photo { width: 218px; height: 127px; box-shadow: 0 8px 10px -6px rgba(0,0,0,.35); }
  .service-name { margin-top: 13px; font-size: 12.5px; line-height: 20px; color: var(--accent-red); font-weight: 400; }
  .service-desc { margin-top: 4px; font-size: 8.2px; line-height: 15px; color: var(--ink-soft); }
  .service-price { margin-top: 8px; font-size: 10px; font-weight: 600; color: var(--sky-blue); display: flex; gap: 24px; }
  .service .btn { margin-top: 8px; }

  /* footer */
  .site-footer { left: 0; top: 1124px; width: 850px; height: 76px; background: var(--footer-bg); }
  .footer-nav { left: 70px; top: 23px; font-size: 9.3px; color: var(--ink); word-spacing: 1px; }
  .footer-nav span { color: var(--ink-soft); padding: 0 7px; }
  .copyright { left: 70px; top: 46px; font-size: 8.3px; color: var(--ink); }
  .social { left: 652px; top: 26px; display: flex; gap: 7px; }
  .social i { width: 27px; height: 27px; border-radius: 50%; display: block; }
</style>
</head>
<body>
  <header class="site-header abs">
    <div class="brand abs"><span class="brand-dot"></span><span class="brand-name">Tidewater Motion Bodywork</span></div>
    <nav class="main-nav abs">
      <a class="is-current" href="#">Home</a><a href="#">Services</a><a href="#">About Us</a><a href="#">Blog</a><a href="#">Contact Us</a>
    </nav>
  </header>

  <div class="hero-band abs"></div>
  <div class="slider-frame abs">
    <div class="slider-photo abs" role="img" aria-label="Therapist giving a sports massage to a client on a treatment table"></div>
    <div class="slider-controls abs">
      <svg width="39" height="27" viewBox="0 0 39 27"><path d="M17 6 L10 13.5 L17 21 M22 6 L29 13.5 L22 21" fill="none" stroke="#777" stroke-width="1.3"/></svg>
    </div>
  </div>

  <h2 class="section-title abs" style="left:70px;top:538px;">Welcome to Massage Practitioner.</h2>
  <div class="intro-photo abs" role="img" aria-label="Athlete celebrating at a race finish line"></div>
  <p class="intro-text abs">Jon turned his passion for sport into a passion for helping athletes. As a Massage Therapist he helps athletes to perform optimally and recover faster from training and racing. Jon is trained in Swedish, Remedial &amp; Sports Massage, Active Release Technique (ART), CORE Mayofascial Release, Emmett Technique, Dry Needeling and Lymphatic Drainage.</p>
  <a class="btn abs" style="left:272px;top:686px;" href="#">READ MORE</a>

  <h2 class="section-title abs" style="left:592px;top:538px;">Testimonials</h2>
  <p class="quote abs"><span class="quote-mark">“</span> Lorem ipsum dolor sit amet, cons ect etur adipiscing elit, sed do eiusmod tempor incididunt ut labore et dolore magna aliqua. Ut enim ad minim veniam, quis nostrud exercitation ullamc.</p>
  <p class="quote-author abs">Jhon Smith, City name</p>

  <div class="divider abs"></div>

  <h2 class="section-title abs" style="left:70px;top:781px;">Services And Pricing</h2>

  <article class="service abs" style="left:70px;top:826px;">
    <div class="service-photo" role="img" aria-label="Therapist working on a client's leg at an event venue" style="background:linear-gradient(135deg,#8b8f94,#3f8fc8 45%,#d8d4d0);"></div>
    <h3 class="service-name">Sport Deep Tissue Massage</h3>
    <p class="service-desc">Lum mleiecneanrit maurillus hertam socatotibus ertas leraeneasmonlusertas lruderugia.</p>
    <div class="service-price"><span>60 mins</span><span>$100</span></div>
    <a class="btn" href="#">READ MORE</a>
  </article>

  <article class="service abs" style="left:316px;top:826px;">
    <div class="service-photo" role="img" aria-label="Close view of myofascial release on an athlete's leg" style="background:linear-gradient(135deg,#5a5048,#a9825e 45%,#26262a 80%);"></div>
    <h3 class="service-name">Myofascial Release</h3>
    <p class="service-desc">Lum mleiecneanrit maurillus hertam socatotibus ertas leraeneasmonlusertas lruderugia.</p>
    <div class="service-price"><span>60 mins</span><span>$120</span></div>
    <a class="btn" href="#">READ MORE</a>
  </article>

  <article class="service abs" style="left:562px;top:826px;">
    <div class="service-photo" role="img" aria-label="Therapists treating an athlete on a massage table" style="background:linear-gradient(135deg,#cfcac4,#8d8780 50%,#4a4744);"></div>
    <h3 class="service-name">Sport Deep Tissue with Active Soft Tissue Work</h3>
    <p class="service-desc">Lum mleiecneanrit maurillus hertam socatotibus</p>
    <div class="service-price"><span>60 mins</span><span>$120</span></div>
    <a class="btn" href="#">READ MORE</a>
  </article>

  <footer class="site-footer abs">
    <p class="footer-nav abs">Home<span>|</span>Services<span>|</span>Our Promise<span>|</span>Treatments<span>|</span>Team<span>|</span>Gallery<span>|</span>Contact us</p>
    <p class="copyright abs">©2015 Massage Practitioner.. All rights reserved privacy policy</p>
    <div class="social abs">
      <i style="background:#27b9e6"></i><i style="background:#c6262b"></i><i style="background:#2f74c0"></i><i style="background:#1a6597"></i>
    </div>
  </footer>
</body>
</html>
```